need corporate, modern business card created for Consulting Company

I need a slick business card using elements from my website, as well as, integrating my pixelforge-created logo (see files).

The business card needs to be:
1. Corporate and modern
2. Clean and professional

I've included a PSD with the logo/icon that you can use to create it. Feel free to try a metallic finish on the logo, make it bigger/small, underlay it. Whatever you need to do to make my card stand out.

Try a black background, or white background or gray.

The idea is for my card to be memorable as well as professional and corporate.

Target Market(s)

Corporate business in the US and Canada.

Industry/Entity Type

Business

Contact Information for Business Card

Commerce Advancing Methods
Martin Coles, Senior Partner
office: 1 877 555 0143
mobile: 1 519 555 0172
website: http://www.brightvale.example

Requirements
Must have
• Card-related information
• corporate, yet modern
• clean and professional
• incorporate the icon only
• must have an editable form when complete!
Nice to have
• metallic icon might be cool
• try it with white or black

```html
<!DOCTYPE html>
<html lang="en">
<head>
<meta charset="utf-8">
<title>Brightvale Business Card</title>
<link rel="stylesheet" href="https://fonts.googleapis.com/css2?family=Exo+2:wght@400;500;600&family=Oswald:wght@500&display=swap">
<style>
  :root {
    --canvas: #e6e6e4;
    --card: #232323;
    --blue: #2f6bb8;
    --white: #ffffff;
    --soft: #d9d9d9;
    --shadow: rgba(0, 0, 0, 0.25);
  }
  * { box-sizing: border-box; margin: 0; padding: 0; }
  html, body {
    width: 1200px; height: 1018px; overflow: hidden;
    background: var(--canvas);
  }
  .sheet { position: relative; width: 1200px; height: 1018px; }
  .card {
    position: absolute; left: 200px;
    width: 800px; height: 457px;
    background: var(--card);
    overflow: hidden;
    box-shadow: 0 10px 28px var(--shadow);
  }
  .card--front { top: 40px; }
  .card--back { top: 521px; }

  .corner-accent { position: absolute; left: 0; top: 0; }

  .brand {
    position: absolute; left: 92px; top: 112px;
    display: flex; align-items: center; gap: 18px;
    transform: rotate(-7deg); transform-origin: left center;
  }
  .brand__square { width: 30px; height: 30px; background: var(--blue); }
  .brand__name {
    font-family: "Exo 2", sans-serif; font-weight: 600;
    font-size: 68px; letter-spacing: 1px;
    color: var(--blue); line-height: 1;
  }

  .contact-band {
    position: absolute; left: -50px; top: 241px;
    width: 900px; height: 78px;
    background: var(--blue);
    transform: rotate(-7deg); transform-origin: center;
    display: grid;
    grid-template-columns: 230px 1fr;
    grid-template-rows: 1fr 1fr;
    align-content: center;
    row-gap: 6px;
    padding: 12px 0 12px 110px;
  }
  .contact-item {
    display: flex; align-items: center; gap: 10px;
    font-family: "Exo 2", sans-serif; font-weight: 400;
    font-size: 15px; letter-spacing: 1px;
    color: var(--white);
  }
  .contact-item svg { width: 15px; height: 15px; flex: none; }

  .person {
    position: absolute; left: 52px; top: 382px;
    color: var(--white);
  }
  .person__name {
    font-family: "Oswald", sans-serif; font-weight: 500;
    font-size: 34px; letter-spacing: 1px; line-height: 1;
    text-transform: uppercase;
  }
  .person__title {
    margin-top: 6px;
    font-family: "Exo 2", sans-serif; font-weight: 500;
    font-size: 15px; letter-spacing: 2px;
    text-transform: uppercase; color: var(--soft);
  }

  .address {
    position: absolute; right: 44px; top: 330px;
    text-align: right;
    font-family: "Exo 2", sans-serif; font-weight: 500;
    font-size: 17px; line-height: 1.45; letter-spacing: 1px;
    color: var(--white);
  }

  .back-band { position: absolute; inset: 0; }
</style>
</head>
<body>
<main class="sheet">

  <section class="card card--front" aria-label="Business card front">
    <svg class="corner-accent" width="170" height="120" viewBox="0 0 170 120" aria-hidden="true">
      <polygon points="0,0 170,0 0,120" fill="var(--blue)"/>
    </svg>

    <div class="brand">
      <span class="brand__square"></span>
      <span class="brand__name">brightvale</span>
    </div>

    <div class="contact-band">
      <span class="contact-item">
        <svg viewBox="0 0 16 16" aria-hidden="true"><path d="M3 1.5l3 3-1.6 1.8a9 9 0 0 0 5.3 5.3L11.5 10l3 3-2 2C6.5 14.5 1.5 9.5 1 3.5z" fill="var(--white)"/></svg>
        1 877 555 0143
      </span>
      <span class="contact-item">
        <svg viewBox="0 0 16 16" aria-hidden="true"><rect x="1.5" y="3" width="13" height="10" fill="var(--white)"/><path d="M1.5 3l6.5 5.5L14.5 3" fill="none" stroke="var(--blue)" stroke-width="1.4"/></svg>
        hello@brightvale.example
      </span>
      <span class="contact-item">
        <svg viewBox="0 0 16 16" aria-hidden="true"><rect x="4" y="1" width="8" height="14" rx="1.5" fill="none" stroke="var(--white)" stroke-width="1.6"/><circle cx="8" cy="12.5" r="0.9" fill="var(--white)"/></svg>
        1 519 555 0172
      </span>
      <span class="contact-item">
        <svg viewBox="0 0 16 16" aria-hidden="true"><circle cx="8" cy="8" r="6.5" fill="none" stroke="var(--white)" stroke-width="1.4"/><ellipse cx="8" cy="8" rx="2.8" ry="6.5" fill="none" stroke="var(--white)" stroke-width="1.2"/><path d="M1.5 8h13M3 4.5h10M3 11.5h10" stroke="var(--white)" stroke-width="1.1"/></svg>
        www.brightvale.example
      </span>
    </div>

    <div class="person">
      <p class="person__name">Martin Coles</p>
      <p class="person__title">Senior Partner</p>
    </div>

    <p class="address">42 Harbor Lane Road,<br>2nd floor Suite 5</p>
  </section>

  <section class="card card--back" aria-label="Business card back">
    <svg class="back-band" width="800" height="457" viewBox="0 0 800 457" aria-hidden="true">
      <polygon points="300,0 430,0 560,457 430,457" fill="var(--blue)"/>
    </svg>
  </section>

</main>
</body>
</html>
```